Production Company need business cards

Hello ! I need a business card for my production company called Brightlane. I put the logo in the files ! This is a brand new production company, modern. We work in the digital industry and have a new and young vision of the content creation. I'll use this business card with a system integrated in it, it will be a digital business card (the type of business card you put behind a phone, and in the phone all your informations will be displayed. You need to respect the colors of the logo for the card (but you can interchange the logo colours to use a black card, or white card, or gold card... You have the .ai file in the files)
In the uploaded files, i puted 2 business card examples, you can see on the cards I just need at the back a small square for a QR code (you can fake it for now).
Target Market(s)
Online business
Industry/Entity Type
Video production
Contact Information for Business Card
Name of the company (Brightlane) , my name (Mathis Verlaeken) and the little square for QR code at the back

```html
<!DOCTYPE html>
<html lang="en">
<head>
<meta charset="utf-8">
<title>Brightlane — Business Cards</title>
<link href="https://fonts.googleapis.com/css2?family=Poppins:wght@300;400;500;600&display=swap" rel="stylesheet">
<style>
  :root {
    --backdrop: #2a2a2a;
    --card: #141414;
    --gold: #d9b32a;
    --white: #f4f4f4;
  }
  html, body {
    margin: 0;
    padding: 0;
    width: 1200px;
    height: 960px;
    overflow: hidden;
    background: var(--backdrop);
    font-family: "Poppins", Arial, sans-serif;
  }
  .stage {
    position: relative;
    width: 1200px;
    height: 960px;
  }
  .card {
    position: absolute;
    left: 250px;
    width: 700px;
    height: 400px;
    background: var(--card);
    box-shadow: 0 12px 30px rgba(0,0,0,0.45);
  }
  .card--front { top: 50px; }
  .card--back { top: 510px; }

  .wordmark {
    position: absolute;
    left: 0;
    right: 0;
    top: 50%;
    transform: translateY(-50%);
    display: flex;
    align-items: center;
    justify-content: center;
    gap: 18px;
  }
  .wordmark__dot {
    width: 22px;
    height: 22px;
    border-radius: 50%;
    background: var(--gold);
  }
  .wordmark__name {
    font-size: 64px;
    font-weight: 500;
    color: var(--gold);
    letter-spacing: 1px;
  }

  .back-brand {
    position: absolute;
    left: 60px;
    top: 110px;
    display: flex;
    align-items: center;
    gap: 12px;
  }
  .back-brand__dot {
    width: 14px;
    height: 14px;
    border-radius: 50%;
    background: var(--gold);
  }
  .back-brand__name {
    font-size: 30px;
    font-weight: 500;
    color: var(--gold);
  }

  .qr-slot {
    position: absolute;
    left: 60px;
    top: 190px;
    width: 110px;
    height: 110px;
    box-sizing: border-box;
    border: 2px solid var(--gold);
    background: #1d1d1d;
  }

  .contact {
    position: absolute;
    right: 48px;
    top: 44px;
    text-align: right;
    color: var(--white);
  }
  .contact__name {
    font-size: 25px;
    font-weight: 600;
    color: var(--gold);
    margin: 0;
    line-height: 1.1;
  }
  .contact__role {
    font-size: 15px;
    font-weight: 500;
    margin: 2px 0 26px;
  }
  .contact__address {
    font-size: 15px;
    font-weight: 300;
    line-height: 1.45;
    margin: 0 0 24px;
    font-style: normal;
  }
  .contact__list {
    list-style: none;
    margin: 0;
    padding: 0;
    font-size: 15px;
    font-weight: 300;
    line-height: 1.6;
  }
  .contact__list li {
    display: flex;
    justify-content: flex-end;
    align-items: center;
    gap: 10px;
  }
  .icon {
    width: 15px;
    height: 15px;
    fill: none;
    stroke: var(--gold);
    stroke-width: 2;
  }
</style>
</head>
<body>
<main class="stage">

  <section class="card card--front" aria-label="Card front">
    <div class="wordmark">
      <span class="wordmark__dot"></span>
      <span class="wordmark__name">Brightlane</span>
    </div>
  </section>

  <section class="card card--back" aria-label="Card back">
    <div class="back-brand">
      <span class="back-brand__dot"></span>
      <span class="back-brand__name">Brightlane</span>
    </div>

    <div class="qr-slot" role="img" aria-label="Reserved square for the digital card QR code"></div>

    <div class="contact">
      <h1 class="contact__name">Mathis Verlaeken</h1>
      <p class="contact__role">Founder &amp; CEO</p>
      <address class="contact__address">1420 Alder Court<br>Fairview, Oregon 97024</address>
      <ul class="contact__list">
        <li>555-214-8830
          <svg class="icon" viewBox="0 0 16 16"><path d="M3 2l3 1 1 3-2 1c1 2 2 3 4 4l1-2 3 1 1 3c-6 1-12-5-11-11z"/></svg>
        </li>
        <li>555-319-4472
          <svg class="icon" viewBox="0 0 16 16"><rect x="4" y="1.5" width="8" height="13" rx="1.5"/></svg>
        </li>
        <li>555-726-1095
          <svg class="icon" viewBox="0 0 16 16"><rect x="2" y="6" width="12" height="7"/><rect x="5" y="2" width="6" height="4"/></svg>
        </li>
        <li>hello@brightlane.co
          <svg class="icon" viewBox="0 0 16 16"><rect x="1.5" y="3.5" width="13" height="9"/><path d="M1.5 3.5l6.5 5 6.5-5"/></svg>
        </li>
        <li>www.brightlane.co
          <svg class="icon" viewBox="0 0 16 16"><circle cx="8" cy="8" r="6.5"/><path d="M1.5 8h13M8 1.5c-3 3-3 10 0 13M8 1.5c3 3 3 10 0 13"/></svg>
        </li>
      </ul>
    </div>
  </section>

</main>
</body>
</html>
```